Tech business card design

We need an amazing business card design for our new business 'Pexla' a marketing tech startup based in Sydney, Australia. We provide an online marketplace for businesses to search and buy advertising media, connect with service providers and learn more about marketing. We wish to communicate 'cool tech', reliability and professionalism and design based around our logo.

Target Market(s)

Business Owners

Contact Information for Business Card

Name
Position
Email Address
Website
Phone Number

Font styles to use
Other font styles liked:
• Avenir & Avenir Next

Colors

Designer to choose colors to be used in the design.

```html
<!DOCTYPE html>
<html lang="en">
<head>
<meta charset="utf-8">
<title>Pexla Business Card</title>
<link rel="stylesheet" href="https://fonts.googleapis.com/css2?family=Nunito+Sans:wght@400;600;800&display=swap">
<style>
  :root {
    --backdrop: #1c1c1e;
    --card-center: #1e2268;
    --card-edge: #0c0e3a;
    --ink: #ffffff;
    --ink-soft: #d9dcf2;
  }
  * { margin: 0; padding: 0; box-sizing: border-box; }
  html, body {
    width: 1200px;
    height: 892px;
    overflow: hidden;
    background: var(--backdrop);
    font-family: "Nunito Sans", "Avenir Next", Avenir, sans-serif;
    color: var(--ink);
  }
  .canvas {
    position: relative;
    width: 1200px;
    height: 892px;
  }
  .card {
    position: absolute;
    width: 560px;
    height: 320px;
    border-radius: 3px;
    background: radial-gradient(ellipse at 45% 40%, var(--card-center) 0%, var(--card-edge) 85%);
    box-shadow: 0 18px 40px rgba(0, 0, 0, 0.55);
  }
  .card--front { left: 90px; top: 70px; }
  .card--back { left: 550px; top: 490px; }

  /* Front */
  .brand {
    position: absolute;
    left: 0; right: 0; top: 78px;
    text-align: center;
    font-weight: 800;
    font-size: 118px;
    line-height: 1;
    letter-spacing: -2px;
    color: var(--ink);
  }
  .front-url {
    position: absolute;
    left: 0; right: 0; top: 232px;
    text-align: center;
    font-size: 13px;
    letter-spacing: 7px;
    color: var(--ink-soft);
  }

  /* Back */
  .identity {
    position: absolute;
    right: 300px;
    top: 138px;
    text-align: right;
    line-height: 1.1;
  }
  .identity__name {
    font-weight: 800;
    font-size: 21px;
    letter-spacing: 0.5px;
  }
  .identity__role {
    font-weight: 400;
    font-size: 16px;
    color: var(--ink-soft);
  }
  .divider {
    position: absolute;
    left: 280px;
    top: 110px;
    width: 1px;
    height: 96px;
    background: linear-gradient(to bottom, transparent, rgba(255,255,255,0.8), transparent);
  }
  .contacts {
    position: absolute;
    left: 298px;
    top: 118px;
    list-style: none;
    font-size: 14px;
    line-height: 22px;
    color: var(--ink-soft);
  }
  .contacts__item {
    display: flex;
    align-items: center;
    gap: 8px;
  }
  .contacts__icon {
    width: 12px;
    height: 12px;
    flex: none;
  }
</style>
</head>
<body>
<main class="canvas">
  <section class="card card--front" aria-label="Card front">
    <div class="brand">pexla</div>
    <div class="front-url">www.pexlamedia.com.au</div>
  </section>

  <section class="card card--back" aria-label="Card back">
    <div class="identity">
      <div class="identity__name">MARCUS DALE</div>
      <div class="identity__role">FOUNDER, DIRECTOR</div>
    </div>
    <div class="divider"></div>
    <ul class="contacts">
      <li class="contacts__item">
        <svg class="contacts__icon" viewBox="0 0 12 12" aria-hidden="true">
          <rect x="3" y="0.5" width="6" height="11" rx="1" fill="none" stroke="#fff" stroke-width="1.2"/>
          <circle cx="6" cy="9.6" r="0.7" fill="#fff"/>
        </svg>
        <span>+61 (0)400 555 018</span>
      </li>
      <li class="contacts__item">
        <svg class="contacts__icon" viewBox="0 0 12 12" aria-hidden="true">
          <rect x="0.5" y="2.5" width="11" height="7.5" fill="#fff"/>
          <path d="M0.5 2.5 L6 7 L11.5 2.5" fill="none" stroke="#0c0e3a" stroke-width="1"/>
        </svg>
        <span>marcus@pexlamedia.com.au</span>
      </li>
      <li class="contacts__item">
        <svg class="contacts__icon" viewBox="0 0 12 12" aria-hidden="true">
          <circle cx="6" cy="6" r="5.5" fill="#fff"/>
          <path d="M6 0.5 V11.5 M0.5 6 H11.5 M6 0.5 C3 3 3 9 6 11.5 C9 9 9 3 6 0.5" fill="none" stroke="#0c0e3a" stroke-width="0.8"/>
        </svg>
        <span>www.pexlamedia.com.au</span>
      </li>
    </ul>
  </section>
</main>
</body>
</html>
```